Design and Renovation Company Luxury Business Card

I want to create a luxury business card for a Design and Renovation Firm . We will use our current logo. The company name is 528BUILDA. We do not want anything standard. We need a very unique concept.
Please see uploaded inspiration. I really like the textured paper option. I would like the card to be thick with debossing, and/or embossing options. The logo has orange in it but I would like to see the card with and without the orange. I think the orange may make the company feel less high-end. The goal is to elevate the logo not match its vibe per se of the logo. We want something very unique, not standard at all!
I would like a space for :
Logo,
Name,
Position,
Email,
Office number,
Website Address,
Business Address,
Thank you!
Have fun!
Target Market(s)
Home owners Age 35 +
Industry/Entity Type
Design and Renovation
Contact Information for Business Card
Logo, Name, Position, Email, Office number, Website Address, Business Address,.
Colors
Designer to choose colors to be used in the design.
Requirements
Must have
- A luxury designer feel. Must be black or dark grey but open to other luxury ideas.
Nice to have
- Gold, silver, black embossing or debossing. Textured paper design.
Should not have
- A cheap look and feel.

```html
<!DOCTYPE html>
<html lang="en">
<head>
<meta charset="utf-8">
<title>528BUILDA Business Card</title>
<link href="https://fonts.googleapis.com/css2?family=Montserrat:wght@400;700&display=swap" rel="stylesheet">
<style>
  :root {
    --backdrop: #5e4e3c;
    --card-white: #ffffff;
    --card-black: #151515;
    --ink: #111111;
    --ink-soft: #222222;
    --accent: #f39220;
    --tile-grey: #e6e6e6;
    --tile-peach: #fff6ee;
    --rule: #333333;
  }
  * { margin: 0; padding: 0; box-sizing: border-box; }
  html, body { width: 900px; height: 1200px; overflow: hidden; }
  body { background: var(--backdrop); position: relative; font-family: "Montserrat", sans-serif; }

  .card { position: absolute; border-radius: 18px; overflow: hidden; box-shadow: 0 10px 24px rgba(0,0,0,.35); }
  .card--front { left: 80px; top: 131px; width: 742px; height: 441px; background: var(--card-white); }
  .card--back { left: 78px; top: 638px; width: 744px; height: 442px; background: var(--card-black); }

  .brand-name { position: absolute; font-family: "Montserrat", sans-serif; font-weight: 700; font-size: 56px; line-height: 1; white-space: nowrap; }
  .card--front .brand-name { left: 34px; top: 66px; color: var(--ink); }
  .card--back .brand-name { left: 0; right: 0; top: 193px; text-align: center; color: var(--card-white); }

  .tile { position: absolute; width: 127px; height: 126px; }
  .tile--peach { left: 568px; top: 31px; background: var(--tile-peach); }
  .tile--grey-left { left: 419px; top: 179px; background: var(--tile-grey); }
  .tile--grey-right { left: 568px; top: 179px; background: var(--tile-grey); }

  .person { position: absolute; left: 34px; top: 255px; color: var(--ink); }
  .person__name { font-weight: 700; font-size: 27px; line-height: 32px; }
  .person__role { font-size: 16.5px; margin-top: 2px; }
  .divider { position: absolute; left: 34px; top: 313px; width: 662px; height: 1.5px; background: var(--rule); }

  .contacts { position: absolute; left: 34px; top: 331px; list-style: none; color: var(--ink-soft); font-size: 16.5px; }
  .contacts li { display: flex; align-items: center; height: 28px; }
  .contacts svg { width: 16px; height: 16px; margin-right: 10px; }

  .address { position: absolute; right: 46px; top: 369px; text-align: right; font-size: 16.5px; line-height: 21px; color: var(--ink-soft); }

  .band { position: absolute; left: 0; bottom: 0; width: 742px; height: 18px; }
</style>
</head>
<body>
  <section class="card card--front">
    <div class="tile tile--peach"></div>
    <div class="tile tile--grey-left"></div>
    <div class="tile tile--grey-right"></div>

    <div class="brand-name">528BUILDA</div>

    <div class="person">
      <div class="person__name">Daniel Reyes</div>
      <div class="person__role">Managing Director</div>
    </div>
    <div class="divider"></div>

    <ul class="contacts">
      <li>
        <svg viewBox="0 0 16 16"><path fill="#f39220" d="M3.2 1.5l2.4 2.6-1.3 1.8c.9 2 2.4 3.6 4.4 4.6l1.8-1.3 2.6 2.4-1.4 2.4C6.6 13.6 2.5 9.4 1 4.2z"/></svg>
        614-555-0148
      </li>
      <li>
        <svg viewBox="0 0 16 16"><rect x="1" y="3.5" width="14" height="9.5" rx="1" fill="#f39220"/><path d="M1.5 4l6.5 5 6.5-5" fill="none" stroke="#fff" stroke-width="1.2"/></svg>
        hello@528builda.com
      </li>
      <li>
        <svg viewBox="0 0 16 16"><circle cx="8" cy="8" r="7" fill="#f39220"/><path d="M1 8h14M8 1c-2.5 2-2.5 12 0 14M8 1c2.5 2 2.5 12 0 14" fill="none" stroke="#fff" stroke-width="1"/></svg>
        www.528builda.com
      </li>
    </ul>

    <div class="address">1180 Maple Grove Ave, #114<br>Dublin, OH 43017</div>

    <svg class="band" viewBox="0 0 742 18" preserveAspectRatio="none">
      <polygon points="0,0 488,0 474,18 0,18" fill="#000"/>
      <polygon points="491,0 742,0 742,18 477,18" fill="#f39220"/>
    </svg>
  </section>

  <section class="card card--back">
    <div class="brand-name">528BUILDA</div>
  </section>
</body>
</html>
```